Torvane Email Signature Banners – Fabrication Capability Series

www.Torvane.com.au is an Australian engineering and fabrication company specialising in fabrication and welding of :
steel piping spools,
skids and frames,
small volume process steel tanks
and general steel fabrication
We require four distinct banner designs for use in Microsoft Lintaro email signatures. Each banner will highlight a specific capability while maintaining a consistent brand identity.
Deliverables
Four banners total:
Piping Spools Fabrication – focus on precision welding and stainless steel pipework
Skid & Frames Fabrication – highlight skid systems and structural frames
Small Steel Tanks Fabrication – show fabricated tanks and workshop craftsmanship
General Fabrication Solutions – broad steel fabrication theme for company-wide use
Dimensions: 600–700 px wide × 100 px high
Format: PNG (preferred), small file size prefered
Resolution: 72 dpi
Background: non-transparent, industrial or workshop setting
Text examples:
1. Piping Spools Fabrication
Option A: “Expert Fabrication Solutions for Process Piping”
Option B: “Precision Welding for Complex Systems”
Option C: “Delivering Quality in Every Spool”
Option D: “Engineered for Flow, Built for Strength”
2. Skid & Frames Fabrication
Option A: “Custom Engineered Modular Systems”
Option B: “Built Strong. Designed Smart.”
Option C: “Reliable Frames for Industrial Performance”
Option D: “Modular Fabrication for Seamless Integration”
3. Small Steel Tanks Fabrication
Option A: “Precision Built for Your Needs”
Option B: “Compact Strength. Proven Durability.”
Option C: “Fabricated for Performance and Longevity”
Option D: “Small Tanks. Big Reliability.”
4. General Fabrication Solutions
Option A: “Quality Craftsmanship, Proven Results”
Option B: “Your Partner in Precision Fabrication”
Option C: “Engineering Excellence in Every Weld”
Option D: “Australian Fabrication. Global Standards.”
Style Direction
Clean, professional, and engineering‑focused
Use Torvane brand colours
Blend photo realism with vector clarity (no heavy gradients)
Include subtle industrial textures or workshop imagery
Typography: bold sans‑serif, legible at small scale
Usage Context
These banners will appear at the bottom of staff email signatures via Lintaro Email Signature Tool for Microsoft 365, so clarity and fast loading are essential. No Logo is required in the banners.
Reference
Existing Torvane signature is attached. Colour palette to match the signature style and logo.
Target Market(s)
Engineering and construction companies,
Industry/Entity Type
Engineering fabrication design
Look and feel

```html
<!DOCTYPE html>
<html lang="en">
<head>
<meta charset="utf-8">
<title>Torvane Fabrication Signature Banners</title>
<link href="https://fonts.googleapis.com/css2?family=Poppins:wght@400;700&display=swap" rel="stylesheet">
<style>
  :root {
    --canvas-bg: #d9d9d9;
    --brand-blue: #4a86c5;
    --brand-deep: #2b5d96;
    --brand-mid: #3d72b0;
    --brand-strong: #1f6fc0;
    --brand-navy: #1d3f66;
    --sky-soft: #c3ddf7;
    --sky-bright: #a6d6f4;
    --accent-text: #cfe1f5;
    --white: #ffffff;
    --photo-steel-a: #4b4f55;
    --photo-steel-b: #7b8088;
    --photo-site-a: #3e434a;
    --photo-site-b: #8a5a4a;
  }
  * { margin: 0; padding: 0; box-sizing: border-box; }
  html, body {
    width: 1200px; height: 128px; overflow: hidden;
    background: var(--canvas-bg);
    font-family: "Poppins", sans-serif;
  }
  .banner {
    position: absolute; top: 24px;
    width: 560px; height: 80px;
    overflow: hidden;
    background: var(--brand-blue);
  }
  .banner--tanks { left: 18px; }
  .banner--spools { left: 618px; }
  .banner-art { position: absolute; inset: 0; width: 560px; height: 80px; }
  .banner-title {
    position: absolute; left: 0; width: 100%;
    text-align: center; color: var(--white);
    font-weight: 700; font-size: 17.6px; line-height: 1;
    letter-spacing: 0.1px; white-space: nowrap;
  }
  .banner-title .highlight { color: var(--accent-text); }
  .banner-tagline {
    position: absolute; left: 0; width: 100%;
    text-align: center; color: var(--white);
    font-weight: 400; font-size: 12px; line-height: 1;
    white-space: nowrap;
  }
  .banner--tanks .banner-title,
  .banner--tanks .banner-tagline { left: 232px; width: 252px; }
  .banner--tanks .banner-title { top: 24px; }
  .banner--tanks .banner-tagline { top: 50px; }
  .banner--spools .banner-title,
  .banner--spools .banner-tagline { left: 198px; width: 268px; }
  .banner--spools .banner-title { top: 19px; }
  .banner--spools .banner-tagline { top: 45px; }
</style>
</head>
<body>

<section class="banner banner--tanks">
  <svg class="banner-art" viewBox="0 0 700 100" preserveAspectRatio="none">
    <defs>
      <linearGradient id="steelTones" x1="0" y1="0" x2="1" y2="1">
        <stop offset="0" stop-color="var(--photo-steel-b)"/>
        <stop offset="1" stop-color="var(--photo-steel-a)"/>
      </linearGradient>
    </defs>
    <path d="M392 -4 L470 -4 Q478 10 462 12 L400 12 Q388 8 392 -4Z" fill="var(--brand-mid)"/>
    <path d="M660 74 Q700 66 706 78 L706 106 L650 106 Q646 80 660 74Z" fill="var(--brand-deep)"/>
    <rect class="photo-fill" x="0" y="0" width="176" height="100" fill="url(#steelTones)" role="img" aria-label="Photo of fabricated steel tank reducers and flanged pipe sections in a workshop"/>
    <polygon points="148,0 172,0 205,50 172,100 148,100 181,50" fill="var(--brand-strong)"/>
    <polyline points="658,21 676,21 676,40" fill="none" stroke="var(--brand-navy)" stroke-width="3"/>
    <polyline points="222,68 222,86 242,86" fill="none" stroke="var(--brand-navy)" stroke-width="3"/>
  </svg>
  <h2 class="banner-title">SMALL <span class="highlight">STEEL TANKS</span> FABRICATION</h2>
  <p class="banner-tagline">Fabricated for Performance and Longevity</p>
</section>

<section class="banner banner--spools">
  <svg class="banner-art" viewBox="0 0 700 100" preserveAspectRatio="none">
    <defs>
      <linearGradient id="siteTones" x1="0" y1="0" x2="1" y2="1">
        <stop offset="0" stop-color="var(--photo-site-a)"/>
        <stop offset="0.7" stop-color="var(--photo-site-a)"/>
        <stop offset="1" stop-color="var(--photo-site-b)"/>
      </linearGradient>
    </defs>
    <path class="photo-fill" d="M0 0 H150 Q186 50 150 100 H0 Z" fill="url(#siteTones)" role="img" aria-label="Photo of workers in safety gear inspecting large lined piping spools on site"/>
    <path d="M150 0 H166 Q204 50 166 100 H150 Q186 50 150 0 Z" fill="var(--sky-soft)"/>
    <rect x="643" y="0" width="30" height="32" rx="3" fill="var(--sky-soft)"/>
    <rect x="643" y="37" width="30" height="28" rx="3" fill="var(--sky-bright)"/>
    <rect x="643" y="70" width="30" height="32" rx="3" fill="var(--brand-navy)"/>
    <rect x="677" y="-3" width="26" height="25" rx="3" fill="var(--brand-strong)"/>
    <rect x="677" y="27" width="26" height="76" rx="3" fill="var(--brand-navy)"/>
    <polyline points="593,14 613,14 613,31" fill="none" stroke="var(--brand-navy)" stroke-width="3"/>
    <polyline points="222,65 222,82 240,82" fill="none" stroke="var(--brand-navy)" stroke-width="3"/>
  </svg>
  <h2 class="banner-title">PIPING SPOOLS FABRICATION</h2>
  <p class="banner-tagline">Expert Fabrication Solutions for Process Piping</p>
</section>

</body>
</html>
```